Brightmill Data Works

Our company is about IT hardwares and IT solutions. IT hardware such as PC, RAMS, storage and servers. IT solutions such as project management, BA. We are also selling new technology too.

Target Market(s)

Consumer, Small to Medium Business, Corporate

Requirements
Must have
• The business card must have the following:
• Name:
• Title:
• Contact Number:
• Email address:
• Website:
• Color: Must match the logo color upgrade

```html
<!DOCTYPE html>
<html lang="en">
<head>
<meta charset="UTF-8">
<title>Brightmill Data Works — Business Card</title>
<link href="https://fonts.googleapis.com/css2?family=Work+Sans:wght@400;500;600;700&display=swap" rel="stylesheet">
<style>
  :root {
    --backdrop: #2f2926;
    --orange-light: #e6922f;
    --orange-dark: #cc6f2c;
    --accent: #dc8a2a;
    --ink: #3a3a3a;
    --ink-soft: #555555;
    --paper: #ffffff;
  }
  * { margin: 0; padding: 0; box-sizing: border-box; }
  html, body { width: 1200px; height: 715px; overflow: hidden; }
  body {
    background: var(--backdrop);
    font-family: "Work Sans", Arial, sans-serif;
    position: relative;
  }
  .card {
    position: absolute;
    top: 203px;
    width: 540px;
    height: 309px;
    border-radius: 3px;
    overflow: hidden;
  }
  .card--front {
    left: 40px;
    background: linear-gradient(135deg, var(--orange-light), var(--orange-dark));
    display: flex;
    align-items: center;
    justify-content: center;
  }
  .card--back {
    left: 620px;
    background: var(--paper);
  }
  .brand {
    display: flex;
    align-items: center;
    gap: 12px;
    font-weight: 700;
    text-transform: uppercase;
    letter-spacing: 0.02em;
    line-height: 1.05;
  }
  .brand__mark { width: 18px; height: 18px; flex: none; }
  .card--front .brand { color: var(--paper); font-size: 34px; }
  .card--front .brand__mark { background: var(--paper); width: 22px; height: 22px; }
  .card--back .brand {
    position: absolute;
    left: 34px;
    top: 118px;
    color: var(--ink);
    font-size: 25px;
  }
  .card--back .brand__mark { background: var(--accent); }
  .divider {
    position: absolute;
    left: 292px;
    top: 70px;
    width: 2px;
    height: 170px;
    background: var(--accent);
  }
  .contact {
    position: absolute;
    left: 314px;
    top: 80px;
    color: var(--ink);
    font-size: 13px;
    line-height: 1.45;
  }
  .contact__name {
    color: var(--accent);
    font-size: 19px;
    font-weight: 500;
    text-transform: uppercase;
    letter-spacing: 0.01em;
  }
  .contact__title { color: var(--ink-soft); font-size: 13px; margin-bottom: 10px; }
  .contact__address { margin-bottom: 8px; }
  .contact__line { display: flex; align-items: center; gap: 7px; }
  .contact__line svg { width: 10px; height: 10px; flex: none; }
  .contact__domain { color: var(--accent); }
</style>
</head>
<body>
  <section class="card card--front">
    <div class="brand"><span class="brand__mark"></span><span>Brightmill<br>Data Works</span></div>
  </section>

  <section class="card card--back">
    <div class="brand"><span class="brand__mark"></span><span>Brightmill<br>Data Works</span></div>
    <div class="divider"></div>
    <div class="contact">
      <p class="contact__name">Daniel Harper</p>
      <p class="contact__title">Director</p>
      <p class="contact__address">220 Orchard Lane Rd<br>Fairview, CA 95110-2231</p>
      <p class="contact__line">
        <svg viewBox="0 0 10 10" aria-hidden="true"><path d="M2 0.5 L3.6 2.6 L2.7 3.6 Q4 6 6.4 7.3 L7.4 6.4 L9.5 8 L8.3 9.5 Q4 9 0.5 1.7 Z" fill="var(--accent)"/></svg>
        555-214-7730
      </p>
      <p class="contact__line">
        <svg viewBox="0 0 10 10" aria-hidden="true"><rect x="0.6" y="2" width="8.8" height="6" fill="none" stroke="var(--accent)" stroke-width="1"/><path d="M0.6 2 L5 5.5 L9.4 2" fill="none" stroke="var(--accent)" stroke-width="1"/></svg>
        info@brightmilldata.com
      </p>
      <p class="contact__line">
        <svg viewBox="0 0 10 10" aria-hidden="true"><circle cx="5" cy="5" r="4.3" fill="none" stroke="var(--accent)" stroke-width="1"/><ellipse cx="5" cy="5" rx="1.9" ry="4.3" fill="none" stroke="var(--accent)" stroke-width="0.8"/><path d="M0.7 5 H9.3" stroke="var(--accent)" stroke-width="0.8"/></svg>
        <span>www.<span class="contact__domain">brightmilldata</span>.com</span>
      </p>
    </div>
  </section>
</body>
</html>
```